Business card for Eyelash extension salon in Beverly Hills,California USA

We need new business card for our salon in Beverly Hills. The salon name is 'Lashvera' . We would like to have...Business name: Lashvera Name of person: will provide later Address 4720 N.Alder Crest Ave Beverly Hills , CA 90210 Phone: will provide later (Text only) Web: www.lashverastudio.example Snapgrid icon, Circlebook icon follow us for seasonal campaign and news @lashverastudiolounge Design should look elegant, high-end, clean, simple, cohesive with my brand. Please refer my brand board. Business name color will be metallic bronzy color. Im thinking grey background or white background. Thanks

Target Market(s)

25-35. Gender neutral. People who are in Entertainment business industry.
This is High-end Eyelash extension salon in Beverly Hills

Industry/Entity Type

Beauty Salon

Contact Information for Business Card

Business name: Lashvera
Name of person: will provide later
Address 4720 N.Alder Crest Ave Beverly Hills , CA 90210
Phone: will provide later (Text only)
Web: www.lashverastudio.example
Snapgrid icon, Circlebook icon
follow us for seasonal campaign and news @lashverastudiolounge

Requirements
Must have
• Beautiful, elegant, clean and simple look but very attractive and modern
Should not have
• We don't like too clutter, too busy designs.

```html
<!DOCTYPE html>
<html lang="en">
<head>
<meta charset="utf-8">
<title>Lashvera Business Card</title>
<link rel="stylesheet" href="https://fonts.googleapis.com/css2?family=Montserrat:wght@400;500;600&family=Playfair+Display:wght@700&display=swap">
<style>
  :root {
    --stage: #e6e4e1;
    --bronze: #8a6850;
    --tan: #c8ad91;
    --mist: #a9a9ab;
    --paper: #ffffff;
    --ink: #4a4543;
    --ink-dark: #2f2b2a;
  }
  * { box-sizing: border-box; margin: 0; padding: 0; }
  html, body { width: 1200px; height: 800px; overflow: hidden; }
  body { background: var(--stage); font-family: "Montserrat", sans-serif; position: relative; }

  .card { position: absolute; width: 630px; height: 360px; overflow: hidden;
          box-shadow: 0 10px 28px rgba(0,0,0,.18); }

  /* Back side */
  .card--back { left: 430px; top: 30px; background: var(--bronze); color: var(--paper); }
  .card--back .brand-name { position: absolute; right: 70px; top: 130px;
          font-size: 46px; font-weight: 500; letter-spacing: 1px; color: var(--paper); }
  .social-row { position: absolute; left: 45px; top: 250px; display: flex; align-items: center;
          gap: 16px; font-size: 14px; font-weight: 500; }
  .social-item { display: flex; align-items: center; gap: 6px; }
  .social-dot { width: 12px; height: 12px; border-radius: 50%; background: var(--paper); }

  /* Front side */
  .card--front { left: 140px; top: 410px; background: var(--paper); }
  .card--front .brand-name { position: absolute; left: 45px; top: 60px;
          font-size: 46px; font-weight: 500; letter-spacing: 1px; color: var(--bronze); }
  .divider { position: absolute; left: 35px; right: 40px; top: 168px; height: 2px; background: var(--bronze); }

  .company { position: absolute; left: 38px; top: 180px; color: var(--ink); }
  .company-name { font-size: 16px; font-weight: 600; color: var(--bronze); letter-spacing: .5px; margin-bottom: 4px; }
  .company-address { font-size: 15px; line-height: 1.4; }

  .person { position: absolute; right: 40px; top: 98px; text-align: right; }
  .person-name { font-family: "Playfair Display", serif; font-weight: 700; font-size: 27px;
          color: var(--bronze); letter-spacing: 1px; }
  .person-title { font-size: 15px; font-weight: 500; color: var(--ink-dark); letter-spacing: 1px; margin-top: 2px; }

  .contact { position: absolute; right: 40px; top: 182px; list-style: none; text-align: right;
          font-size: 15px; color: var(--ink); line-height: 1.6; }
  .contact li { display: flex; justify-content: flex-end; align-items: center; gap: 10px; }
  .contact .accent { color: var(--bronze); }
  .contact svg { width: 12px; height: 12px; fill: none; stroke: var(--bronze); stroke-width: 1.6; }

  .waves { position: absolute; left: 0; bottom: 0; width: 630px; height: 360px; }
</style>
</head>
<body>

<section class="card card--back" aria-label="Card back">
  <div class="brand-name">Lashvera</div>
  <div class="social-row">
    <span class="social-item"><span class="social-dot"></span>Snapgrid</span>
    <span class="social-item"><span class="social-dot"></span>Circlebook</span>
    <span class="social-handle">@lashverastudiolounge</span>
  </div>
</section>

<section class="card card--front" aria-label="Card front">
  <svg class="waves" viewBox="0 0 630 360" preserveAspectRatio="none" aria-hidden="true">
    <path fill="var(--mist)" d="M0,228 C60,300 200,310 360,300 C480,292 580,290 630,300 V360 H0Z"/>
    <path fill="var(--tan)" d="M0,250 C70,310 210,318 360,310 C480,304 580,305 630,318 V360 H0Z"/>
    <path fill="var(--bronze)" d="M0,278 C90,322 220,332 360,324 C480,318 580,326 630,342 V360 H0Z"/>
  </svg>

  <div class="brand-name">Lashvera</div>

  <div class="person">
    <div class="person-name">MAREN HOLLOWAY</div>
    <div class="person-title">GESCHAFTSFUHRER</div>
  </div>

  <div class="divider"></div>

  <div class="company">
    <div class="company-name">LASHVERA</div>
    <div class="company-address">4720 N.Alder Crest Ave<br>Beverly Hills , CA 90210</div>
  </div>

  <ul class="contact">
    <li>0176 555 0192
      <svg viewBox="0 0 12 12"><path d="M3 1 L5 3 L4 4.5 C5 6.5 6 7.5 7.5 8 L9 7 L11 9 L9.5 11 C5 10.5 1.5 7 1 2.5 Z"/></svg>
    </li>
    <li>holloway@orvani.example
      <svg viewBox="0 0 12 12"><rect x="1" y="2.5" width="10" height="7"/><path d="M1 2.5 L6 6.5 L11 2.5"/></svg>
    </li>
    <li><span>www.<span class="accent">lashverastudio</span>.example</span>
      <svg viewBox="0 0 12 12"><circle cx="6" cy="6" r="5"/><ellipse cx="6" cy="6" rx="2.2" ry="5"/><path d="M1 6 H11"/></svg>
    </li>
  </ul>
</section>

</body>
</html>
```